WordPress Site That Reviews Footwear

We need a wordpress web design for an affiliate site called PaceKite. We review and do roundups on footwear products. The final design should be clean and mobile friendly. The site should be built with Gutenberg page builder. We like the design of https://lunavessel.com/.
Updates

Need extra days to review

Target Market(s)

USA

Industry/Entity Type

Footwear

Logo Text

PaceKite

Number of Pages Required

4 page

Font styles to use
Serif
Sans Serif

Requirements
Must have
• Wordpress site
Blog post
Page
Categories
Homepage

```html
<!DOCTYPE html>
<html lang="en">
<head>
<meta charset="utf-8">
<title>PaceKite – Expert footwear advice</title>
<link href="https://fonts.googleapis.com/css2?family=Playfair+Display:wght@400;700&family=Roboto:wght@400;500;700&display=swap" rel="stylesheet">
<style>
:root{
  --ink:#111;
  --text:#2a2a2a;
  --page:#f7f7f7;
  --card:#ffffff;
  --slate:#4b6676;
  --band:#cfe0ea;
  --review-card:#eef3f7;
  --star:#f2b417;
  --footer:#0a0a0a;
  --serif:'Playfair Display', Georgia, serif;
  --sans:'Roboto', Arial, sans-serif;
}
*{box-sizing:border-box;margin:0;padding:0}
html,body{width:1200px;height:2865px;overflow:hidden}
body{background:var(--page);font-family:var(--sans);color:var(--text);position:relative}
a{color:inherit}
.nw{white-space:nowrap}

/* header */
.site-header{position:absolute;top:0;left:0;width:1200px;height:63px;background:#fff;border-bottom:1px solid #e5e5e5}
.brand{position:absolute;left:111px;top:10px;font-family:var(--serif);font-weight:700;font-size:34px;color:var(--ink);letter-spacing:.2px;white-space:nowrap}
.main-nav{position:absolute;left:351px;top:21px;width:600px;display:flex;justify-content:space-between;font-size:15px;color:#222;white-space:nowrap}
.social{display:flex;gap:6px}
.social span{width:37px;height:37px;border:1px solid #333;border-radius:50%;display:block}
.site-header .social{position:absolute;left:963px;top:11px}

/* hero */
.hero{position:absolute;top:63px;left:0;width:1200px;height:549px;
  background:linear-gradient(180deg,#6f78a4 0%,#8a80a8 35%,#b78aa6 60%,#5a4c66 78%,#2b2732 100%)}
.hero .shoe{position:absolute;right:0;top:0;width:720px;height:549px;
  background:radial-gradient(ellipse at 70% 30%,rgba(40,48,44,.85) 0%,rgba(60,90,60,.55) 35%,rgba(120,180,80,.15) 60%,transparent 75%)}
.hero h1{position:absolute;left:111px;top:138px;font-family:var(--serif);font-weight:400;font-size:49px;line-height:52px;color:#fff;white-space:nowrap}
.hero p{position:absolute;left:111px;top:256px;font-size:16.5px;line-height:26px;color:#fff;font-weight:500;white-space:nowrap}
.hero .cta{position:absolute;left:110px;top:336px;width:342px;height:52px;border:1px solid #fff;color:#fff;
  font-size:16px;font-weight:500;display:flex;align-items:center;justify-content:center;gap:8px;white-space:nowrap}

/* section titles */
.sec-title{position:absolute;left:0;width:1200px;text-align:center;font-family:var(--serif);font-weight:400;color:var(--ink)}
.sec-sub{position:absolute;left:0;width:1200px;text-align:center;font-size:17.5px;line-height:23px;color:#222}

/* footwear type */
.type-photo{position:absolute;left:111px;top:813px;width:328px;height:384px;border-radius:10px;
  background:linear-gradient(135deg,#eee7e2 0%,#d9bfae 45%,#c89d86 70%,#f3efec 100%)}
.type-item{position:absolute;width:300px;height:180px}
.type-item h3{font-family:var(--serif);font-weight:400;font-size:22px;color:#222;margin-bottom:8px;white-space:nowrap}
.type-item p{font-size:13px;line-height:25px;color:#333;white-space:nowrap;letter-spacing:-.2px}
.pill{position:absolute;left:-5px;top:124px;display:flex;align-items:center;justify-content:center;width:200px;height:40px;border-radius:20px;
  background:var(--slate);color:#fff;font-size:15px;white-space:nowrap}

/* results */
.result-card{position:absolute;top:1398px;width:236px;height:187px;background:var(--card);border-radius:5px;padding:16px 13px}
.result-card svg{display:block;width:50px;height:50px;margin-bottom:4px}
.result-card h3{font-family:var(--serif);font-weight:400;font-size:22px;color:#222;margin-bottom:4px}
.result-card p{font-size:12.5px;line-height:25px;color:#333;white-space:nowrap;letter-spacing:-.2px}

/* reviews */
.reviews{position:absolute;top:1678px;left:0;width:1200px;height:415px;background:var(--band)}
.reviews h2,.learn h2{font-family:var(--serif);font-weight:400;font-size:31px;color:#222;position:absolute;left:114px;white-space:nowrap}
.reviews h2{top:64px}
.score{position:absolute;left:114px;top:105px;display:flex;align-items:center;gap:6px}
.score b{font-size:34px;font-weight:700;color:#111}
.score small{font-size:13px;line-height:14px;color:#222}
.stars{position:absolute;left:113px;top:142px;display:flex;gap:2px}
.side-text{position:absolute;left:114px;font-size:16px;line-height:23px;color:#333;white-space:nowrap}
.side-btn{position:absolute;left:110px;width:210px;height:41px;border-radius:21px;background:var(--slate);color:#fff;
  font-size:16px;display:flex;align-items:center;justify-content:center;white-space:nowrap}
.review-card{position:absolute;top:65px;width:232px;height:286px;background:var(--review-card);border-radius:4px;padding:18px 18px}
.review-card .rater{text-align:center;font-weight:500;font-size:30px;color:var(--slate);letter-spacing:-.5px;line-height:34px}
.review-card .rating-line{text-align:center;font-size:8px;color:#555;margin-top:1px}
.review-card .mini-stars{display:flex;justify-content:center;gap:2px;margin-top:2px}
.review-card .who{font-size:13px;font-weight:500;color:#111;margin-top:14px}
.review-card .when{font-size:11px;color:#444;margin-top:2px}
.review-card .body{font-size:12px;line-height:20.5px;color:#444;margin-top:13px;white-space:nowrap;letter-spacing:-.1px}
.read-more{font-size:13.5px;text-decoration:underline;color:#222;display:inline-block;margin-top:12px;white-space:nowrap}

/* learn */
.learn{position:absolute;top:2093px;left:0;width:1200px;height:439px}
.learn h2{top:89px;line-height:32px}
.post{position:absolute;top:89px;width:232px}
.post .thumb{width:232px;height:159px}
.post .tag{font-size:12px;font-weight:500;color:#222;margin-top:19px;white-space:nowrap}
.post h3{font-family:var(--serif);font-weight:400;font-size:18.5px;line-height:21px;color:#222;margin-top:6px;white-space:nowrap}
.post .read-more{margin-top:13px}

/* footer */
.site-footer{position:absolute;top:2532px;left:0;width:1200px;height:333px;background:var(--footer);color:#fff}
.site-footer .brand{color:#fff;top:63px;left:113px}
.site-footer .social{position:absolute;left:134px;top:118px}
.site-footer .social span{border-color:#bbb}
.fcol{position:absolute;top:70px;white-space:nowrap}
.fcol h4{font-size:19px;font-weight:700;letter-spacing:.2px;margin-bottom:12px}
.fcol a{display:block;text-decoration:none;font-size:16px;line-height:33px}
.fcol p{font-size:12.5px;line-height:26px;letter-spacing:-.2px}
.fine{position:absolute;top:281px;left:111px;width:978px;border-top:1px solid #333;padding-top:17px;text-align:center;font-size:13.5px}
</style>
</head>
<body>

<header class="site-header">
  <div class="brand">PaceKite</div>
  <nav class="main-nav">
    <span>PRODUCTS</span><span>FOOTWEAR TYPE</span><span>CONCERNS</span><span>REVIEWS</span><span>ABOUT</span><span>CONTACT</span>
  </nav>
  <div class="social" aria-label="Social links"><span></span><span></span><span></span></div>
</header>

<section class="hero">
  <div role="img" aria-label="Close-up of a running shoe mid-stride above an airport runway at dusk" style="position:absolute;inset:0"></div>
  <div class="shoe" aria-hidden="true"></div>
  <h1>Expert footwear advice,<br>based on science</h1>
  <p>Lorem ipsum dolor sit amet, consectetur adipiscing<br>elit, sed do eiusmod tempor incididunt</p>
  <div class="cta">CHECK OUT A FEW OF OUR FAVORITES
    <svg width="10" height="10" viewBox="0 0 10 10"><path d="M1 1l4 4-4 4M5 1l4 4-4 4" fill="none" stroke="#fff" stroke-width="1.4"/></svg>
  </div>
</section>

<h2 class="sec-title" style="top:690px;font-size:36px">What’s your footwear type?</h2>
<p class="sec-sub" style="top:742px">Sed ut perspiciatis unde omnis iste natus error sit voluptatem<br>accusantium dolorem</p>

<div class="type-photo" role="img" aria-label="Hands placing a cushioned insole under a bare foot"></div>

<div class="type-item" style="left:476px;top:822px">
  <h3>The standard Sed</h3>
  <p>Lorem ipsum dolor sit amconsectetur adipiscing elit,<br>d do eiusmod tempor incididunt ut labore et dLorem<br>ipsum dolor sit amconsectetur adipiscing</p>
  <div class="pill">THAT’S ME</div>
</div>
<div class="type-item" style="left:795px;top:822px">
  <h3>The standard Sed</h3>
  <p>Lorem ipsum dolor sit amconsectetur adipiscing elit,<br>d do eiusmod tempor incididunt ut labore et dLorem<br>ipsum dolor sit amconsectetur adipiscing</p>
  <div class="pill">GIVE ME TIPS</div>
</div>
<div class="type-item" style="left:476px;top:1017px">
  <h3>The standard Sed</h3>
  <p>Lorem ipsum dolor sit amconsectetur adipiscing elit,<br>d do eiusmod tempor incididunt ut labore et dLorem<br>ipsum dolor sit amconsectetur adipiscing</p>
  <div class="pill">SOUNDS ABOUT RIGHT</div>
</div>
<div class="type-item" style="left:795px;top:1017px">
  <h3>The standard Sed</h3>
  <p>Lorem ipsum dolor sit amconsectetur adipiscing elit,<br>d do eiusmod tempor incididunt ut labore et dLorem<br>ipsum dolor sit amconsectetur adipiscing</p>
  <div class="pill">START TREATING</div>
</div>

<h2 class="sec-title" style="top:1270px;font-size:37px">Finally... Footwear advice that gets results.</h2>
<p class="sec-sub" style="top:1322px">Sed ut perspiciatis unde omnis iste natus error sit voluptatem<br>accusantium dolorem</p>

<div class="result-card" style="left:111px">
  <svg viewBox="0 0 50 50" fill="none" stroke="#222" stroke-width="1.8"><rect x="3" y="3" width="18" height="42" rx="9"/><rect x="24" y="12" width="18" height="35" rx="9"/><ellipse cx="12" cy="30" rx="4" ry="8"/><ellipse cx="33" cy="34" rx="4" ry="7"/></svg>
  <h3>The standard</h3>
  <p>Lorem ipsum dolor sit amconsectetur<br>adipiscing elit, d do eiusmod tempor<br>incididunt ut labore et d</p>
</div>
<div class="result-card" style="left:358px">
  <svg viewBox="0 0 50 50" fill="none" stroke="#222" stroke-width="1.8"><circle cx="25" cy="16" r="9"/><circle cx="25" cy="16" r="4"/><circle cx="12" cy="34" r="4"/><circle cx="25" cy="32" r="4"/><circle cx="38" cy="34" r="4"/><path d="M5 48v-6a7 7 0 0114 0v6M18 48v-8a7 7 0 0114 0v8M31 48v-6a7 7 0 0114 0v6"/></svg>
  <h3>The standard</h3>
  <p>Lorem ipsum dolor sit amconsectetur<br>adipiscing elit, d do eiusmod tempor<br>incididunt ut labore et d</p>
</div>
<div class="result-card" style="left:606px">
  <svg viewBox="0 0 50 50" fill="none" stroke="#222" stroke-width="1.8"><path d="M4 8l8-4 10 12 20 14a6 6 0 01-2 10L28 40 4 20z"/><path d="M8 22l24 20M14 12l6 6M20 20l4-4M26 26l4-4"/></svg>
  <h3>The standard</h3>
  <p>Lorem ipsum dolor sit amconsectetur<br>adipiscing elit, d do eiusmod tempor<br>incididunt ut labore et d</p>
</div>
<div class="result-card" style="left:853px">
  <svg viewBox="0 0 50 50" fill="none" stroke="#222" stroke-width="1.8"><circle cx="25" cy="16" r="9"/><circle cx="25" cy="16" r="4"/><circle cx="12" cy="34" r="4"/><circle cx="25" cy="32" r="4"/><circle cx="38" cy="34" r="4"/><path d="M5 48v-6a7 7 0 0114 0v6M18 48v-8a7 7 0 0114 0v8M31 48v-6a7 7 0 0114 0v6"/></svg>
  <h3>The standard</h3>
  <p>Lorem ipsum dolor sit amconsectetur<br>adipiscing elit, d do eiusmod tempor<br>incididunt ut labore et d</p>
</div>

<section class="reviews">
  <h2>Our Reviews</h2>
  <div class="score"><b>5.0</b><small>Out of<br>5 Stars</small></div>
  <div class="stars">
    <svg width="200" height="38" viewBox="0 0 200 38" fill="#f2b417"><defs><path id="st" d="M19 1l5.3 11.6 12.7 1.4-9.5 8.6 2.6 12.5L19 28.8 7.9 35.1l2.6-12.5L1 14l12.7-1.4z"/></defs><use href="#st"/><use href="#st" x="40"/><use href="#st" x="80"/><use href="#st" x="120"/><use href="#st" x="160"/></svg>
  </div>
  <p class="side-text" style="top:195px">Sed ut perspiciatis unde omnis<br>iste ts error sit voluptate</p>
  <div class="side-btn" style="top:258px">Leave Us Feedback</div>

  <div class="review-card" style="left:350px">
    <div class="rater">Ratewise</div>
    <div class="rating-line">5 Star Customer Rating</div>
    <div class="mini-stars"><svg width="80" height="15" viewBox="0 0 200 38" fill="#f2b417"><use href="#st"/><use href="#st" x="40"/><use href="#st" x="80"/><use href="#st" x="120"/><use href="#st" x="160"/></svg></div>
    <div class="who">Dana Rowe</div>
    <div class="when">April 3,2021</div>
    <p class="body">Lorem ipsum dolor siet, consectetur<br>adipiscing elit, sed do eiuod tempor<br>incididunt ut labore et dolore magna<br>aliqua. Quis ipsum suspendisse</p>
    <a class="read-more">Read More »</a>
  </div>
  <div class="review-card" style="left:603px">
    <div class="rater">Ratewise</div>
    <div class="rating-line">5 Star Customer Rating</div>
    <div class="mini-stars"><svg width="80" height="15" viewBox="0 0 200 38" fill="#f2b417"><use href="#st"/><use href="#st" x="40"/><use href="#st" x="80"/><use href="#st" x="120"/><use href="#st" x="160"/></svg></div>
    <div class="who">Dana Rowe</div>
    <div class="when">April 3,2021</div>
    <p class="body">Lorem ipsum dolor siet, consectetur<br>adipiscing elit, sed do eiuod tempor<br>incididunt ut labore et dolore magna<br>aliqua. Quis ipsum suspendisse</p>
    <a class="read-more">Read More »</a>
  </div>
  <div class="review-card" style="left:856px">
    <div class="rater">Ratewise</div>
    <div class="rating-line">5 Star Customer Rating</div>
    <div class="mini-stars"><svg width="80" height="15" viewBox="0 0 200 38" fill="#f2b417"><use href="#st"/><use href="#st" x="40"/><use href="#st" x="80"/><use href="#st" x="120"/><use href="#st" x="160"/></svg></div>
    <div class="who">Dana Rowe</div>
    <div class="when">April 3,2021</div>
    <p class="body">Lorem ipsum dolor siet, consectetur<br>adipiscing elit, sed do eiuod tempor<br>incididunt ut labore et dolore magna<br>aliqua. Quis ipsum suspendisse</p>
    <a class="read-more">Read More »</a>
  </div>
</section>

<section class="learn">
  <h2>Learn from the<br>experts.</h2>
  <p class="side-text" style="top:170px">Sed ut perspiciatis unde omnis<br>iste ts error sit voluptatemorem<br>que laudantium, totam rem<br>aperiam, eaque ipsa</p>
  <div class="side-btn" style="top:283px">Get Better Footwear</div>

  <article class="post" style="left:350px">
    <div class="thumb" role="img" aria-label="Tan leather hiking boots standing on snowy ground" style="background:linear-gradient(135deg,#7a5a3c 0%,#c98a3c 45%,#e6e1dc 100%)"></div>
    <div class="tag">FEATURES 3 WEEKS AGO</div>
    <h3>The standard Lorem Ipsum<br>passage, used the 1500</h3>
    <a class="read-more">Read More »</a>
  </article>
  <article class="post" style="left:602px">
    <div class="thumb" role="img" aria-label="Shoemaker in a workshop holding a finished sneaker" style="background:linear-gradient(135deg,#5a4a52 0%,#8a7f86 50%,#b3a9a6 100%)"></div>
    <div class="tag">FEATURES 3 WEEKS AGO</div>
    <h3>The standard Lorem Ipsum<br>passage, used the 1500</h3>
    <a class="read-more">Read More »</a>
  </article>
  <article class="post" style="left:854px">
    <div class="thumb" role="img" aria-label="White cycling shoe on a black background" style="background:radial-gradient(ellipse at 55% 65%,#9a9a98 0%,#3a3a3a 35%,#0c0c0c 70%)"></div>
    <div class="tag">FEATURES 3 WEEKS AGO</div>
    <h3>The standard Lorem Ipsum<br>passage, used the 1500</h3>
    <a class="read-more">Read More »</a>
  </article>
</section>

<footer class="site-footer">
  <div class="brand">PaceKite</div>
  <div class="social" aria-label="Social links"><span></span><span></span><span></span></div>
  <div class="fcol" style="left:330px"><h4>ABOUT</h4><a>About</a><a>Contact</a><a>Media</a></div>
  <div class="fcol" style="left:444px"><h4>COMPANY</h4><a>Terms of Use</a><a>Privacy Policy</a><a>Editorial Policy</a><a>How We Make Money</a></div>
  <div class="fcol" style="left:643px"><h4>DISCOVER</h4><a>Products</a><a>Footwear Type</a><a>Footwear Concerns</a><a>Reviews</a></div>
  <div class="fcol" style="left:829px"><h4>HOW WE MAKE MONEY</h4><p>Lorem ipsumlor sit amet, consectur adipiscing<br>elit, sed do eiusmod tempor incididunt ut labore<br>et dolore magna aliqua. Quis ium suspendisse<br>ultrices gravida.</p></div>
  <div class="fine">Copyright © 2021 PaceKite. All rights</div>
</footer>

</body>
</html>
```